Wedding Ceremony Equipment Hire Business Card

I need a business card design for a new business I created called Vowline Rentals. We hire out Wedding Ceremony equipment and decorations mainly for beach and garden wedding ceremonies that include delivery, set up and dismantle. We do offer DIY Chair Hire as well.
I'd like to have a similar design and colours to our website:
www.vowlinerentals.com.au
If possible would like the front to incorporate our information and logo and the back to have two faded example pictures of our wedding ceremonies.
I have attached two photos and our logo. Please let me know if you need a better pic of our logo though.

Target Market(s)

Newly engaged couples, aged 25 and upwards

Industry/Entity Type

Wedding

Contact Information for Business Card

Vowline Rentals
Mira Holt
0412 908 146
hello@vowlinerentals.com.au
www.vowlinesocial.com/VowlineRentals

```html
<!DOCTYPE html>
<html lang="en">
<head>
<meta charset="utf-8">
<title>Vowline Rentals – Business Card</title>
<link rel="stylesheet" href="https://fonts.googleapis.com/css2?family=Cormorant+Garamond:ital,wght@0,500;1,400&display=swap">
<style>
  :root {
    --page: #ffffff;
    --card: #1b1f20;
    --band: #8cfc9c;
    --ink-dark: #1b1f20;
    --ink-mint: #a9f7b4;
    --ornament: #6f7a7c;
  }
  * { margin: 0; padding: 0; box-sizing: border-box; }
  html, body {
    width: 1200px;
    height: 741px;
    overflow: hidden;
    background: var(--page);
  }
  .card {
    position: absolute;
    left: 70px;
    top: 82px;
    width: 1060px;
    height: 575px;
    background: var(--card);
    overflow: hidden;
  }
  .brand-band {
    position: absolute;
    left: 0;
    top: 201px;
    width: 100%;
    height: 173px;
    background: var(--band);
  }
  .flourish {
    position: absolute;
    left: 0;
    top: 0;
    width: 540px;
    height: 575px;
  }
  .brand-name {
    position: absolute;
    left: 230px;
    top: 252px;
    width: 600px;
    text-align: center;
    font-family: "Cormorant Garamond", Georgia, serif;
    font-weight: 500;
    font-size: 60px;
    line-height: 70px;
    color: var(--ink-dark);
  }
  .contact {
    position: absolute;
    left: 680px;
    top: 386px;
    width: 360px;
    text-align: center;
    font-family: "Cormorant Garamond", Georgia, serif;
    font-style: italic;
    color: var(--ink-mint);
  }
  .contact__name {
    font-size: 38px;
    line-height: 50px;
  }
  .contact__rule {
    width: 348px;
    height: 3px;
    margin: 8px auto 8px;
    background: var(--ink-mint);
    border: 0;
  }
  .contact__phone {
    font-size: 21px;
    line-height: 24px;
  }
  .contact__line {
    font-size: 18px;
    line-height: 22.5px;
  }
</style>
</head>
<body>
  <div class="card">
    <div class="brand-band"></div>

    <svg class="flourish" role="img" aria-label="Decorative swirl flourish in soft grey" viewBox="0 0 540 575">
      <defs>
        <radialGradient id="flourish-tone" cx="45%" cy="45%" r="60%">
          <stop offset="0%" stop-color="var(--ornament)" stop-opacity="0.45"/>
          <stop offset="100%" stop-color="var(--ornament)" stop-opacity="0.12"/>
        </radialGradient>
      </defs>
      <rect width="540" height="575" fill="url(#flourish-tone)"/>
    </svg>

    <div class="brand-name">Vowline Rentals</div>

    <div class="contact">
      <div class="contact__name">Mira Holt</div>
      <hr class="contact__rule">
      <div class="contact__phone">Call us: 0412 908 146</div>
      <div class="contact__line">hello@vowlinerentals.com.au</div>
      <div class="contact__line">www.vowlinerentals.com.au</div>
      <div class="contact__line">www.vowlinesocial.com/VowlineRentals</div>
    </div>
  </div>
</body>
</html>
```